Real Estate Business Card

On the front side I want to have my info, my brokerage info.
On the back side I want have my complany’s logo, website and Facebook link. I will provide all this once I select a design.

I would like to see Black background and gold text, Dark Blue and gold text and White and blue text designs

Font styles to use
Sans Serif
Script

```html
<!DOCTYPE html>
<html lang="en">
<head>
<meta charset="utf-8">
<title>Northpeak Realty – Business Card</title>
<link href="https://fonts.googleapis.com/css2?family=Roboto:wght@400;500;700;900&display=swap" rel="stylesheet">
<style>
  :root {
    --backdrop: #2b2b2d;
    --card: #1c1c1e;
    --band-red: #d2353c;
    --band-red-dark: #b8262d;
    --gold: #e2b64a;
    --gold-soft: #d9a93a;
    --ink-white: #f2f2f2;
    --logo-slate: #8c96ad;
  }
  * { box-sizing: border-box; margin: 0; padding: 0; }
  html, body {
    width: 1200px; height: 900px; overflow: hidden;
    background: var(--backdrop);
    font-family: "Roboto", Arial, sans-serif;
  }
  .canvas { position: relative; width: 1200px; height: 900px; }
  .card {
    position: absolute; width: 740px; height: 410px;
    background: var(--card);
    box-shadow: 0 14px 30px rgba(0,0,0,.45);
    overflow: hidden;
  }
  .card--back { left: 290px; top: 25px; }
  .card--front { left: 170px; top: 465px; }

  .brand {
    position: absolute; white-space: nowrap;
    font-weight: 900; color: var(--logo-slate);
    text-transform: uppercase; line-height: 1; letter-spacing: 1px;
  }
  .card--back .brand { right: 48px; bottom: 52px; font-size: 38px; }
  .card--front .brand { right: 52px; top: 232px; font-size: 34px; }

  .name-band {
    position: absolute; left: 0; top: 70px; width: 610px; height: 62px;
    background: linear-gradient(90deg, var(--band-red-dark), var(--band-red));
    padding: 8px 0 0 48px;
  }
  .person__name {
    color: var(--gold); font-weight: 700; font-size: 27px; letter-spacing: .5px; line-height: 1;
  }
  .person__title {
    color: var(--gold-soft); font-weight: 500; font-size: 18px; margin-top: 4px; line-height: 1;
  }

  .address {
    position: absolute; left: 78px; top: 205px;
    color: var(--ink-white); font-size: 19px; line-height: 1.3;
  }
  .contact-list {
    position: absolute; left: 56px; top: 272px; list-style: none;
    color: var(--ink-white); font-size: 19px;
  }
  .contact-list li { display: flex; align-items: center; gap: 12px; height: 28px; }
  .contact-list svg { width: 18px; height: 18px; flex: none; }
</style>
</head>
<body>
<main class="canvas">

  <section class="card card--back" aria-label="Card back">
    <p class="brand">Northpeak Realty</p>
  </section>

  <section class="card card--front" aria-label="Card front">
    <div class="name-band">
      <p class="person__name">DANIEL REYES</p>
      <p class="person__title">CEO/FOUNDER</p>
    </div>

    <p class="brand">Northpeak Realty</p>

    <p class="address">2140 Birchwood Drive<br>Fairbanks, Alaska 99701</p>

    <ul class="contact-list">
      <li>
        <svg viewBox="0 0 24 24" aria-hidden="true"><path fill="var(--gold)" d="M6.6 10.8a15.1 15.1 0 0 0 6.6 6.6l2.2-2.2c.3-.3.7-.4 1-.2 1.1.4 2.3.6 3.6.6.6 0 1 .4 1 1V20c0 .6-.4 1-1 1A17 17 0 0 1 3 4c0-.6.4-1 1-1h3.5c.6 0 1 .4 1 1 0 1.3.2 2.5.6 3.6.1.3 0 .7-.2 1z"/></svg>
        <span>555 210 4836</span>
      </li>
      <li>
        <svg viewBox="0 0 24 24" aria-hidden="true"><rect x="2" y="5" width="20" height="14" fill="var(--gold)"/><path d="M2 5l10 8 10-8" fill="none" stroke="var(--card)" stroke-width="1.6"/></svg>
        <span>dan@northpeakhomes.com</span>
      </li>
      <li>
        <svg viewBox="0 0 24 24" aria-hidden="true"><circle cx="12" cy="12" r="10" fill="var(--gold)"/><path d="M2 12h20M12 2c3 3 3 17 0 20M12 2c-3 3-3 17 0 20" fill="none" stroke="var(--card)" stroke-width="1.4"/></svg>
        <span>www.northpeakhomes.com</span>
      </li>
      <li>
        <svg viewBox="0 0 24 24" aria-hidden="true"><circle cx="12" cy="12" r="10" fill="var(--gold)"/></svg>
        <span>/northpeakhomes</span>
      </li>
    </ul>
  </section>

</main>
</body>
</html>
```